Zestora - Landing Page

Need a landing page for a journal app. The app is based on a retrospective board, where each journal entry is split into 3 sections: "What went well", "What Didn't Go Well" and "Things To Try".
The landing page should match the style of all modern web application landing pages. Think Brint, Tivalo, Mirvane. I've included screenshots of the app.
One feature that I want to highlight that is not ready yet, is an AI coach. It will offer insights based on the history of the user's journal entries
1 page

```html
<!DOCTYPE html>
<html lang="en">
<head>
<meta charset="utf-8">
<title>Zestora – Journal App</title>
<link rel="stylesheet" href="https://fonts.googleapis.com/css2?family=Outfit:wght@300;400;500;600;700&family=Inter:wght@400;500;600&display=swap">
<style>
:root{
  --blue:#0b4fb0;
  --blue-deep:#0a47a0;
  --ink:#1c1f26;
  --body:#5b6070;
  --tint:#edf2fa;
  --white:#ffffff;
  --side:#1f2836;
  --line:#e3e6ec;
  --green:#4caf50;
  --field:#f4f5f7;
}
*{box-sizing:border-box;margin:0;padding:0}
html,body{width:1200px;height:3138px;overflow:hidden}
body{position:relative;font-family:"Outfit",sans-serif;color:var(--ink);background:var(--white)}
.abs{position:absolute}
a{color:inherit;text-decoration:none}

/* header + hero */
.hero-band{left:0;top:0;width:1200px;height:619px;background:linear-gradient(180deg,#0a4aa8,#0c52b6)}
.tint-band{left:0;top:619px;width:1200px;height:1722px;background:linear-gradient(160deg,#f3f7fd 0%,#e7eef9 40%,#eef3fb 100%)}
.cta-band{left:0;top:2341px;width:1200px;height:374px;background:var(--white)}
.footer{left:0;top:2715px;width:1200px;height:423px;background:var(--blue)}

.brand{font-weight:700;color:var(--white);letter-spacing:-.3px}
.nav{top:25px;left:431px;display:flex;gap:0;color:var(--white);font-size:16px;font-weight:400}
.nav a{position:absolute;white-space:nowrap}
.nav .active::before{content:"";position:absolute;left:0;right:0;top:-25px;height:4px;background:var(--white)}
.login{left:838px;top:26px;color:var(--white);font-size:16px;display:flex;align-items:center;gap:7px}
.btn{display:flex;align-items:center;justify-content:center;border-radius:22px;font-size:16px;font-weight:400}
.btn-light{background:var(--white);color:var(--blue)}
.btn-ghost{border:2px solid var(--white);color:var(--white)}
.btn-blue{background:var(--blue);color:var(--white)}

.hero-title{left:0;width:1200px;text-align:center;color:var(--white);font-size:41px;line-height:52px}
.hero-title b{font-weight:700}
.hero-title span{font-weight:300}

/* app frames */
.frame{background:var(--white);border:6px solid #e9ebf0;border-radius:18px;overflow:hidden;box-shadow:0 18px 40px rgba(20,40,90,.18)}
.side{position:absolute;left:0;top:0;bottom:0;width:34px;background:var(--side)}
.side i{position:absolute;left:11px;width:11px;height:9px;border:1.5px solid #c9ced8;border-radius:2px}
.side .logo-dot{left:10px;top:10px;width:12px;height:12px;background:#7ac943;border:none;border-radius:3px}
.side .avatar{left:8px;bottom:6px;top:auto;width:17px;height:17px;border-radius:50%;background:#d7dbe2;border:none}
.side .on{background:#3b4657}
.entry-title{font-family:"Inter",sans-serif;font-weight:600;color:var(--ink)}
.meta{font-family:"Inter",sans-serif;color:#444;display:flex;align-items:center;gap:8px}
.tag{border-radius:10px;color:var(--white);font-weight:600;padding:2px 8px}
.col{position:absolute;border:1px solid var(--line);border-radius:4px;background:var(--white)}
.col-head{font-family:"Inter",sans-serif;color:#333;display:flex;align-items:center;gap:8px}
.col-head::before{content:"";width:8px;height:7px;background:#5b7bd5;border-radius:1px}
.toolbar{position:absolute;background:var(--field);border:1px solid var(--line);font-family:"Inter",sans-serif;color:#444}
.editor{position:absolute;border:1px solid var(--line);background:var(--white);font-family:"Inter",sans-serif;color:#333}
.editor ul{list-style:none}
.editor li{position:relative}
.editor li::before{content:"•";position:absolute;left:-7px}

/* feature copy */
.h2{font-size:44px;line-height:53px;color:var(--ink);letter-spacing:-.3px}
.h2 b{font-weight:700}
.h2 span{font-weight:400}
.para{font-size:15.6px;line-height:25.7px;color:var(--body);font-weight:300;width:445px}
.more{font-size:15.5px;font-weight:600;color:var(--blue);border-bottom:1.5px solid var(--blue);display:flex;align-items:center;gap:3px;padding-bottom:1px}
.accent{background:var(--blue);border-radius:16px}

/* list mock */
.list-card{position:absolute;border:1px solid var(--line);background:var(--white);font-family:"Inter",sans-serif;font-size:7.4px;line-height:11px;color:#333;padding:10px 12px}
.list-card h5{font-size:8.6px;font-weight:600;margin-bottom:4px}
.list-card .sub{color:#999}

/* dashboard mock */
.dash{font-family:"Inter",sans-serif;color:#222}
.card{position:absolute;background:var(--white);border-radius:8px;box-shadow:0 4px 14px rgba(30,40,70,.09)}
.tiny{font-size:6px;color:#999}
.lbl{font-size:8.5px;font-weight:600}
.prog{height:3px;background:#e5e7eb;border-radius:2px;position:relative}
.prog i{position:absolute;left:0;top:0;height:3px;border-radius:2px}

/* cta */
.cta-h{left:0;width:1200px;text-align:center;font-size:43px;line-height:52px}
.stars{color:#f5a623;letter-spacing:2px}

/* footer */
.f-col h4{font-size:21px;font-weight:600;color:var(--white);position:relative;padding-bottom:14px}
.f-col h4::after{content:"";position:absolute;left:0;bottom:0;width:28px;height:2px;background:var(--white)}
.f-col ul{list-style:none;margin-top:16px}
.f-col li{font-size:16.5px;line-height:25.7px;color:var(--white);font-weight:300}
.f-text{color:var(--white);font-size:16.5px;line-height:26px;font-weight:300}
.social{display:flex;gap:14px;color:var(--white);font-size:13px;font-weight:400;align-items:center}
.social span{display:flex;align-items:center;gap:5px}
.social span::before{content:"";width:7px;height:7px;border-radius:50%;background:var(--white)}
</style>
</head>
<body>

<div class="abs hero-band"></div>
<div class="abs tint-band"></div>
<div class="abs cta-band"></div>
<div class="abs footer"></div>

<!-- header -->
<div class="abs brand" style="left:110px;top:18px;font-size:25px">Zestora</div>
<nav class="abs nav">
  <a class="active" style="left:0">Home</a>
  <a style="left:74px">Products</a>
  <a style="left:169px">Solutions</a>
  <a style="left:264px">Resources</a>
</nav>
<div class="abs login">
  <svg width="17" height="17" viewBox="0 0 17 17" fill="none" stroke="#fff" stroke-width="1.5"><circle cx="8.5" cy="5.5" r="3.5"/><path d="M2 16c0-3.6 2.9-6 6.5-6s6.5 2.4 6.5 6"/></svg>Login
</div>
<a class="abs btn btn-light" style="left:937px;top:18px;width:150px;height:41px">Get Started</a>

<!-- hero -->
<h1 class="abs hero-title" style="top:146px"><b>Made for people.</b><br><span>Built for productivity</span></h1>
<a class="abs btn btn-light" style="left:442px;top:260px;width:151px;height:40px">Get Started</a>
<a class="abs btn btn-ghost" style="left:605px;top:260px;width:150px;height:40px">Find Your Plan</a>

<div class="abs frame" style="left:201px;top:329px;width:797px;height:460px">
  <div class="side"><i class="logo-dot"></i><i class="on" style="top:46px"></i><i style="top:68px"></i><i style="top:90px"></i><i class="avatar"></i></div>
  <div class="abs entry-title" style="left:92px;top:16px;font-size:12px">Entry</div>
  <div class="abs meta" style="left:100px;top:40px;font-size:8px">▦ Thu Aug 22 2024 ⌄ <span class="tag" style="background:var(--green);font-size:7px">Gym</span></div>

  <div class="col" style="left:92px;top:80px;width:207px;height:357px">
    <div class="col-head abs" style="left:10px;top:11px;font-size:8px">What Went Well?</div>
    <div class="toolbar" style="left:8px;top:35px;width:189px;height:30px;font-size:7.5px;padding:4px 6px;line-height:11px">Normal ⌃ &nbsp; B I U S ”<br>☰ ☰ ☰ ☰ &nbsp;T</div>
    <div class="editor" style="left:11px;top:76px;width:184px;height:264px;font-size:9px;line-height:13.8px;padding:5px 8px 0 22px"><ul><li>Completed all scheduled workouts this week.</li><li>Increased bench press weight by 10 pounds.</li><li>Maintained consistent energy levels throughout sessions.</li></ul></div>
  </div>
  <div class="col" style="left:325px;top:80px;width:207px;height:357px">
    <div class="col-head abs" style="left:10px;top:11px;font-size:8px">What Didn't Go Well?</div>
    <div class="toolbar" style="left:8px;top:35px;width:189px;height:30px;font-size:7.5px;padding:4px 6px;line-height:11px">Normal ⌃ &nbsp; B I U S ”<br>☰ ☰ ☰ ☰ &nbsp;T</div>
    <div class="editor" style="left:11px;top:76px;width:184px;height:264px;font-size:9px;line-height:13.8px;padding:5px 8px 0 22px"><ul><li>Struggled with form on deadlifts, leading to lower back discomfort.</li><li>Missed two stretching sessions after workouts.</li><li>Skipped meal prep, resulting in inconsistent nutrition.</li></ul></div>
  </div>
  <div class="col" style="left:558px;top:80px;width:207px;height:357px">
    <div class="col-head abs" style="left:10px;top:11px;font-size:8px">Things To Try</div>
    <div class="toolbar" style="left:8px;top:35px;width:189px;height:30px;font-size:7.5px;padding:4px 6px;line-height:11px">Normal ⌃ &nbsp; B I U S ”<br>☰ ☰ ☰ ☰ &nbsp;T</div>
    <div class="editor" style="left:11px;top:76px;width:184px;height:264px;font-size:9px;line-height:13.8px;padding:5px 8px 0 22px"><ul><li>Focus on deadlift form by lowering the weight and reviewing proper technique.</li><li>Set reminders for post-workout stretching to prevent muscle tightness.</li><li>Dedicate Sunday evenings to meal prep to ensure a balanced diet.</li></ul></div>
  </div>
</div>

<!-- feature 1 -->
<h2 class="abs h2" style="left:112px;top:905px"><b>The fastest way to get</b><br><span>tasks out of your head.</span></h2>
<p class="abs para" style="left:112px;top:1016px">Lorem ipsum dolor sit amet, consectetur adipiscing elit, sed do eiusmod tempor incididunt ut labore et dolore magna aliqua. Ut enim ad minim veniam, quis nostrud exercitation ullamco laboris nisi ut aliquip ex ea commodo consequat. Duis aute irure dolor in reprehenderit in voluptate velit esse cillum dolore eu fugiat nulla pariatur. Excepteur sint occaecat cupidatat</p>
<a class="abs more" style="left:112px;top:1187px">Find Out More ⟶</a>

<div class="abs accent" style="left:1023px;top:843px;width:87px;height:152px"></div>
<div class="abs frame" style="left:597px;top:866px;width:496px;height:382px">
  <div class="side"><i class="logo-dot"></i><i class="on" style="top:34px"></i><i style="top:52px"></i><i style="top:70px"></i><i class="avatar"></i></div>
  <div class="abs entry-title" style="left:70px;top:6px;font-size:10px">Entry</div>
  <div class="abs meta" style="left:78px;top:26px;font-size:6.5px">▦ Wed Aug 21 2024 ⌄ <span class="tag" style="background:#2f3a4a;font-size:6px">Default Journal</span></div>
  <div class="col" style="left:71px;top:58px;width:172px;height:300px">
    <div class="col-head abs" style="left:8px;top:8px;font-size:6.5px">What Went Well?</div>
    <div class="toolbar" style="left:6px;top:28px;width:158px;height:25px;font-size:6px;padding:3px 5px;line-height:9px">Normal ⌃ &nbsp; B I U S ”<br>☰ ☰ ☰ ☰ &nbsp;T</div>
    <div class="editor" style="left:9px;top:62px;width:154px;height:226px"></div>
  </div>
  <div class="col" style="left:265px;top:58px;width:172px;height:300px">
    <div class="col-head abs" style="left:8px;top:8px;font-size:6.5px">What Didn't Go Well?</div>
    <div class="toolbar" style="left:6px;top:28px;width:158px;height:25px;font-size:6px;padding:3px 5px;line-height:9px">Normal ⌃ &nbsp; B I U S ”<br>☰ ☰ ☰ ☰ &nbsp;T</div>
    <div class="editor" style="left:9px;top:62px;width:154px;height:226px"></div>
  </div>
  <div class="col" style="left:459px;top:58px;width:172px;height:300px">
    <div class="toolbar" style="left:6px;top:28px;width:158px;height:25px"></div>
    <div class="editor" style="left:9px;top:62px;width:154px;height:226px"></div>
  </div>
</div>

<!-- feature 2 -->
<div class="abs accent" style="left:91px;top:1318px;width:87px;height:152px"></div>
<div class="abs frame" style="left:107px;top:1340px;width:498px;height:378px">
  <div class="side" style="width:28px"><i class="logo-dot" style="left:8px"></i><i class="on" style="top:30px;left:8px"></i><i style="top:48px;left:8px"></i><i style="top:66px;left:8px"></i><i class="avatar" style="left:5px"></i></div>
  <div class="abs" style="left:84px;top:26px;border:1px solid var(--line);border-radius:3px;font-family:Inter,sans-serif;font-size:7px;padding:3px 7px;font-weight:500">+ Add New</div>
  <div class="list-card" style="left:84px;top:62px;width:410px;height:250px">
    <h5>Thu Aug 22 2024</h5>
    <div class="sub">What Went Well</div>
    Completed all scheduled workouts this week.<br>Increased bench press weight by 10 pounds.<br>Maintained consistent energy levels throughout sessions.
    <div class="sub">What Didn't Go Well</div>
    Struggled with form on deadlifts, leading to lower back discomfort.<br>Missed two stretching sessions after workouts.<br>Skipped meal prep, resulting in inconsistent nutrition.
    <div class="sub">Things To Try</div>
    Focus on deadlift form by lowering the weight and reviewing proper technique.<br>Set reminders for post-workout stretching to prevent muscle tightness.<br>Dedicate Sunday evenings to meal prep to ensure a balanced diet.
  </div>
  <div class="list-card" style="left:84px;top:320px;width:410px;height:60px">
    <h5>Tue Aug 20 2024</h5>
    <div class="sub">What Went Well</div>
    Achieved a personal best in squats, adding 15 pounds.
  </div>
</div>
<h2 class="abs h2" style="left:646px;top:1350px"><b>Reach that mental</b><br><span>clarity you’ve been<br>longing for.</span></h2>
<p class="abs para" style="left:646px;top:1512px">Lorem ipsum dolor sit amet, consectetur adipiscing elit, sed do eiusmod tempor incididunt ut labore et dolore magna aliqua. Ut enim ad minim veniam, quis nostrud exercitation ullamco laboris nisi ut aliquip ex ea commodo consequat. Duis aute irure dolor in reprehenderit in voluptate velit esse cillum dolore eu fugiat nulla pariatur.</p>
<a class="abs more" style="left:646px;top:1677px">Find Out More ⟶</a>

<!-- feature 3 -->
<h2 class="abs h2" style="left:112px;top:1870px"><b>AI</b> <span>Coach</span></h2>
<p class="abs para" style="left:112px;top:1946px">Lorem ipsum dolor sit amet, consectetur adipiscing elit, sed do eiusmod tempor incididunt ut labore et dolore magna aliqua. Ut enim ad minim veniam, quis nostrud exercitation ullamco laboris nisi ut aliquip ex ea commodo consequat. Duis aute irure dolor in reprehenderit in voluptate velit esse cillum dolore eu fugiat nulla pariatur. Excepteur sint occaecat cupidatat</p>
<a class="abs more" style="left:112px;top:2111px">Find Out More ⟶</a>

<div class="abs accent" style="left:1027px;top:2066px;width:86px;height:152px"></div>
<div class="abs frame dash" style="left:597px;top:1817px;width:496px;height:380px;background:#fafbfc">
  <div class="abs lbl" style="left:12px;top:14px;font-size:8px">Dashboard</div>
  <div class="abs tiny" style="left:28px;top:44px">Project</div>
  <div class="abs" style="left:4px;top:64px;width:70px;height:16px;background:#1f2836;border-radius:3px;color:#fff;font-size:6px;padding:4px 0 0 26px">Statistics</div>
  <div class="abs tiny" style="left:28px;top:98px">Media</div>
  <div class="abs tiny" style="left:28px;top:124px">Dashboard</div>
  <div class="abs tiny" style="left:28px;top:150px">Reports</div>
  <div class="abs tiny" style="left:28px;top:350px">Settings</div>
  <div class="abs" style="left:107px;top:20px;width:22px;height:22px;border-radius:50%;background:#d9dce2"></div>
  <div class="abs lbl" style="left:137px;top:22px">User Name</div>
  <div class="abs tiny" style="left:137px;top:33px">Member</div>

  <div class="card" style="left:107px;top:74px;width:90px;height:132px">
    <div class="abs lbl" style="left:10px;top:10px;font-size:7.5px">Category name</div>
    <div class="abs tiny" style="left:10px;top:36px">JAN</div>
    <div class="abs" style="left:10px;top:44px;font-size:11px;font-weight:700">12k</div>
    <svg class="abs" style="left:44px;top:40px" width="32" height="22"><rect x="0" y="12" width="5" height="10" fill="#3bbf6e"/><rect x="7" y="8" width="5" height="14" fill="#3bbf6e"/><rect x="14" y="4" width="5" height="18" fill="#3bbf6e"/><rect x="21" y="0" width="5" height="22" fill="#3bbf6e"/></svg>
    <div class="abs tiny" style="left:10px;top:86px">FEB</div>
    <div class="abs" style="left:10px;top:94px;font-size:11px;font-weight:700">1.2m</div>
    <svg class="abs" style="left:44px;top:92px" width="32" height="22"><rect x="0" y="10" width="5" height="12" fill="#3bbf6e"/><rect x="7" y="6" width="5" height="16" fill="#3bbf6e"/><rect x="14" y="12" width="5" height="10" fill="#3bbf6e"/><rect x="21" y="2" width="5" height="20" fill="#3bbf6e"/></svg>
  </div>
  <div class="card" style="left:204px;top:74px;width:92px;height:132px">
    <div class="abs lbl" style="left:10px;top:10px;font-size:7.5px">Category</div>
    <div class="abs" style="left:10px;top:40px;font-size:17px;font-weight:500">1282</div>
    <svg class="abs" style="left:8px;top:72px" width="78" height="36"><path d="M0 28 C10 28 12 14 22 16 S32 30 42 20 S56 2 66 10 S74 20 78 14" fill="none" stroke="#3bbf6e" stroke-width="1.6"/></svg>
  </div>
  <div class="card" style="left:349px;top:72px;width:124px;height:62px;background:#1f2430">
    <div class="abs" style="left:14px;top:10px;font-size:5.5px;color:#bbb">Progress</div>
    <div class="abs" style="left:14px;top:18px;font-size:13px;font-weight:700;color:#fff">4751</div>
    <div class="abs" style="left:90px;top:22px;font-size:6px;color:#ddd">75.5%</div>
    <div class="abs prog" style="left:14px;top:42px;width:96px;background:#444"><i style="width:72px;background:#cfd3da"></i></div>
  </div>
  <div class="card" style="left:349px;top:150px;width:124px;height:190px">
    <div class="abs lbl" style="left:12px;top:12px;font-size:7.5px">Category name</div>
    <div class="abs tiny" style="left:12px;top:42px">Lorem ipsum</div><div class="abs" style="left:84px;top:40px;font-size:7px;font-weight:600">40%</div>
    <div class="abs prog" style="left:12px;top:54px;width:86px"><i style="width:42px;background:#1f2430"></i></div>
    <div class="abs tiny" style="left:12px;top:80px">Dolor</div><div class="abs" style="left:84px;top:78px;font-size:7px;font-weight:600">35%</div>
    <div class="abs prog" style="left:12px;top:92px;width:86px"><i style="width:42px;background:#3bbf6e"></i></div>
    <div class="abs tiny" style="left:12px;top:118px">Sit amet</div><div class="abs" style="left:84px;top:116px;font-size:7px;font-weight:600">15%</div>
    <div class="abs prog" style="left:12px;top:130px;width:86px"><i style="width:18px;background:#2f6fe0"></i></div>
    <div class="abs tiny" style="left:12px;top:156px">Consectetur</div><div class="abs" style="left:84px;top:154px;font-size:7px;font-weight:600">10%</div>
    <div class="abs prog" style="left:12px;top:168px;width:86px"><i style="width:14px;background:#9aa1ad"></i></div>
  </div>
  <div class="card" style="left:107px;top:240px;width:189px;height:104px">
    <div class="abs lbl" style="left:10px;top:10px;font-size:7.5px">Category name</div>
    <div class="abs tiny" style="left:10px;top:34px;line-height:21px;font-size:5.5px;color:#333">Lorem ipsum<br>Dolor<br>Sit amet</div>
    <div class="abs tiny" style="left:70px;top:34px;line-height:21px;font-size:5.5px">04/02/2021<br>03/02/2021<br>02/02/2021</div>
    <div class="abs tiny" style="left:112px;top:34px;line-height:21px;font-size:5.5px;color:#3bbf6e">+432<br>+31<br><span style="color:#999">-75</span></div>
    <div class="abs tiny" style="left:150px;top:34px;line-height:21px;font-size:5.5px;color:#222">$322<br>$173<br>$456</div>
  </div>
</div>

<!-- CTA -->
<h2 class="abs cta-h" style="top:2416px"><b style="font-weight:700">Gain calmness and clarity with the world’s</b><br><span style="font-weight:400">most beloved productivity app</span></h2>
<div class="abs" style="left:0;width:1200px;top:2532px;text-align:center;font-size:16.5px;color:var(--ink)">374000+ <span class="stars">★★★★★</span> reviews on Playden and Appvault</div>
<a class="abs btn btn-blue" style="left:528px;top:2583px;width:151px;height:40px">Start for free</a>

<!-- footer -->
<div class="abs brand" style="left:127px;top:2816px;font-size:33px">Zestora</div>
<p class="abs f-text" style="left:127px;top:2859px">Join millions of people who organize<br>work and life with Zestora.</p>
<div class="abs social" style="left:127px;top:2934px"><span>Sociva</span><span>Pictro</span><span>Linkara</span><span>Vidora</span></div>

<div class="abs f-col" style="left:483px;top:2803px"><h4>Features</h4><ul><li>How It Works</li><li>For Teams</li><li>Pricing</li><li>Templates</li></ul></div>
<div class="abs f-col" style="left:697px;top:2803px"><h4>Resources</h4><ul><li>Download Apps</li><li>Help Center</li><li>Productivity Methods</li><li>Integrations</li><li>Channel Partners</li><li>Developer API</li><li>Status</li></ul></div>
<div class="abs f-col" style="left:945px;top:2803px"><h4>Company</h4><ul><li>About Us</li><li>Careers</li><li>Inspiration Hub</li><li>Press</li><li>Threadly</li></ul></div>

<div class="abs f-text" style="left:128px;top:3076px">Security &nbsp;| &nbsp;Privacy &nbsp;| &nbsp;Terms</div>
<div class="abs f-text" style="left:772px;top:3076px">© Copyrights 2024 | All Rights Reserved</div>

</body>
</html>
```